Promotion for a free HTML weather widget

skyvantor (http://www.skyvantor.example/) is a meteorological service based in Basel, Switzerland.
We offer a free HTML widget that offers weather forecasts for a selected location anywhere on the world for up to seven days (see http://www.skyvantor.example/en_GB/weather/forecast/widgetsetup) which can be included in any other website.
To make the widget more popular and well-known, we would like to add a promotional banner for it on our own homepage. The space where the banner will be located is marked red on the attached banner_location.png.
We have received permissions from three websites that are already using our widget to use a screenshot from their website on this banner.
These websites are:
- http://gazette.plorix.example/ (widget is on the bottom of the page)
- http://www.tonvillage.example/
- http://www.valtrun.example/
Requirements
Must have
- - Width: 696px
- Height: 150px to 200px
- fits nicely in our website
- uses screenshots of the three aforementioned websites (widget must be visible, other ads on those website must be unrecognisable)
- Text (English) that praises the most important advantages of the widget: it is free to use, worldwide available, easy to integrate, offers valuable weather information to visitors
- Possibility to change the text on our side for translations

```html
<!DOCTYPE html>
<html lang="en">
<head>
<meta charset="utf-8">
<title>skyvantor forecast – Basel</title>
<link href="https://fonts.googleapis.com/css2?family=Arimo:wght@400;700&family=Ubuntu:wght@400;500&display=swap" rel="stylesheet">
<style>
:root{
  --page:#e8e8e8; --panel:#f7f7f7; --border:#c9c9c9; --text:#111; --muted:#8a8a8a;
  --link:#1a6fd1; --topbar:#8eb4dc; --tab:#3c5f86; --tab-active:#f7f7f7;
  --t19:#ffff00; --t25:#ffcc00; --t29:#ff9a00; --t32:#ff6a00; --t27:#ff9a00;
  --band:#a9cff0; --band-text:#fff; --banner-dark:#4d5258; --banner-mid:#7c8187;
  --cold:#cfff8a; --warm:#ffe14d; --rain:#1a6fd1; --brand:#f2f2f2;
}
*{box-sizing:border-box;margin:0;padding:0}
html,body{width:1200px;height:1020px;overflow:hidden;background:var(--page)}
body{font-family:"Arimo",Arial,sans-serif;color:var(--text)}
.stage{position:absolute;left:0;top:0;width:1305px;height:1109px;transform:scale(.9195);transform-origin:0 0}
.abs{position:absolute}
.topbar{left:0;top:0;width:1305px;height:20px;background:linear-gradient(#a8c6e6,var(--topbar))}
.tabs{left:158px;top:0;width:697px;height:20px;display:flex}
.tab{flex:1;background:var(--tab);display:flex;align-items:center;gap:8px;padding-left:12px;border-right:1px solid #2c4b6e}
.tab.active{background:var(--tab-active)}
.tab .ic{width:14px;height:14px;border:2px solid #fff;border-radius:50%}
.tab.active .ic{border-color:#333}
.tab .bar{width:54px;height:6px;background:#8fa3b8;position:relative}
.tab .bar i{position:absolute;left:0;top:0;height:6px;background:#f2d500}
.tab.active .bar i{background:#5bb300}
.panel{background:var(--panel);border:1px solid var(--border)}
.forecast{left:158px;top:20px;width:698px;height:411px}
.row{position:absolute;left:10px;display:flex;align-items:center;font-size:14.5px}
.row .label{width:275px}
.row .cell{width:58px;text-align:center}
.row .arrow{font-size:17px;font-weight:700}
.blue{color:var(--link)}
.icon{width:48px;height:42px;margin:0 5px;border:1px solid #9bb;}
.day{background:linear-gradient(#6ab8ff,#9fd2ff)}
.night{background:linear-gradient(#0d2446,#234a7a)}
.storm{background:linear-gradient(#304a6a,#8a9aae)}
.temp{display:inline-block;width:48px;height:28px;line-height:28px;font-weight:700;font-size:14.5px}
.ring{width:48px;height:42px;margin:0 5px;border:1px solid #555;background:#fff}
.sun{left:11px;top:37px;width:66px;height:42px;display:flex}
.uv{width:24px;height:42px;background:#1d3d8c;color:#fff;font-size:12px;font-weight:700;text-align:center;padding-top:3px}
.uv b{display:block;color:#e01010;font-size:14px}
.sunimg{width:42px;height:42px;background:radial-gradient(circle,#fff 10%,#7fc4ff 60%,#3a86d6)}
.moonimg{left:125px;top:37px;width:42px;height:42px;background:#000}
.times{font-size:12.5px;line-height:21px}
.band{left:10px;top:348px;width:355px;height:19px;background:var(--band);border-radius:0 14px 14px 0;color:var(--band-text);font-size:14px;display:flex;align-items:center}
.band span{display:flex;align-items:center;gap:7px;padding-left:2px;width:222px}
.band span::before{content:"";width:15px;height:15px;background:#6d9fc9}
.tools{left:10px;top:382px;display:flex;font-size:14.5px;color:var(--muted)}
.tools span{display:flex;align-items:center;gap:7px;width:222px}
.tools span::before{content:"";width:17px;height:17px;background:#9a9a9a}
.radar{left:158px;top:441px;width:698px;height:245px}
.radar h2{position:absolute;left:10px;top:3px;font-size:20px;font-weight:700;color:#333}
.radar .rule{left:0;top:30px;width:696px;height:1px;background:#ddd}
.map{background:linear-gradient(135deg,#d7d7d7,#a9a9a9);border:1px solid #999}
.radar p{font-size:14.5px;line-height:21px}
.banner{left:160px;top:696px;width:696px;height:199px;border:1px solid #888;background:#fff}
.promo{left:1px;top:1px;width:367px;height:195px;background:radial-gradient(circle at 70% 40%,var(--banner-mid),var(--banner-dark))}
.promo .art{left:6px;top:4px;width:160px;height:160px;border-radius:50%;background:radial-gradient(circle,#e8e8e8 30%,rgba(200,200,200,.2) 70%,transparent)}
.brand{left:152px;top:16px;font-family:"Ubuntu",sans-serif;font-weight:500;font-size:30px;color:var(--brand)}
.tagline{left:153px;top:50px;font-family:"Ubuntu",sans-serif;font-size:14px;color:#e8e8e8}
.perks{left:180px;top:72px;list-style:none;font-family:"Ubuntu",sans-serif;font-size:16px;color:#fff;line-height:22px}
.perks li::before{content:"•";margin-left:-14px;margin-right:8px}
.days{left:368px;top:1px;width:176px;height:195px;display:flex;justify-content:space-around;padding-top:6px;font-family:"Ubuntu",sans-serif}
.d{width:50px;text-align:center}
.d .n{font-size:21px;color:#333}
.d .dt{font-size:11px;font-weight:700;margin:3px 0 6px}
.d .wi{width:50px;height:44px;border-radius:4px;background:linear-gradient(#74b9f5,#a8d4fa)}
.d .wi.cloud{background:linear-gradient(#7fa8d2,#b9c8d8)}
.d .hi,.d .lo{height:30px;margin-top:5px;line-height:30px;font-size:20px;font-weight:500;border-radius:2px}
.d .hi{background:var(--warm)}
.d .lo{background:var(--cold)}
.d small{font-size:10px}
.d .mm{color:var(--rain);font-size:16px;margin-top:6px}
.users{left:544px;top:1px;width:150px;height:195px;background:linear-gradient(#6a6f75,#8c9196);font-family:"Ubuntu",sans-serif;color:#fff}
.users .hd{position:absolute;left:22px;top:8px;color:#f2cf3a;font-size:14px;font-weight:500}
.users .nm{position:absolute;font-weight:500}
.side{left:878px;top:6px;width:300px;height:180px;background:#fff;border:1px solid var(--border);padding:10px}
.side h3{font-size:16.5px;font-weight:400;margin-bottom:8px}
.side p{font-size:12.5px;line-height:15px;text-align:justify}
.more{left:878px;top:195px;font-size:14.5px;color:#333;line-height:20px}
.more ul{padding-left:20px}
</style>
</head>
<body>
<div class="stage">
  <div class="abs topbar"></div>
  <div class="abs tabs">
    <div class="tab active"><span class="ic"></span><span class="bar"><i style="width:100%"></i></span></div>
    <div class="tab"><span class="ic"></span><span class="bar"><i style="width:55%"></i></span></div>
    <div class="tab"><span class="ic"></span><span class="bar"><i style="width:55%"></i></span></div>
    <div class="tab"><span class="ic"></span><span class="bar"><i style="width:40%"></i></span></div>
    <div class="tab"><span class="ic"></span><span class="bar"><i style="width:55%"></i></span></div>
    <div class="tab"><span class="ic"></span><span class="bar"><i style="width:55%"></i></span></div>
    <div class="tab"><span class="ic"></span><span class="bar"><i style="width:75%;background:#8cc400"></i></span></div>
  </div>

  <section class="abs panel forecast">
    <div class="row" style="top:10px"><span class="label">Monday, 05.08 (CEST)</span>
      <span class="cell">05:00</span><span class="cell">08:00</span><span class="cell">11:00</span><span class="cell">14:00</span><span class="cell">17:00</span><span class="cell">20:00</span><span class="cell">23:00</span></div>
    <div class="abs sun"><div class="uv">UV<b>8</b></div><div class="sunimg" role="img" aria-label="Sun symbol"></div></div>
    <div class="abs times" style="left:78px;top:37px">↑06:15<br>↓20:55</div>
    <div class="abs moonimg" role="img" aria-label="Moon phase symbol"></div>
    <div class="abs times" style="left:168px;top:37px">↑04:52<br>↓19:45</div>
    <div class="row" style="top:37px"><span class="label"></span>
      <span class="icon night" role="img" aria-label="Clear night"></span><span class="icon day" role="img" aria-label="Sunny"></span><span class="icon day" role="img" aria-label="Sunny, thin haze"></span><span class="icon day" role="img" aria-label="Sunny, thin haze"></span><span class="icon day" role="img" aria-label="Sunny, thin haze"></span><span class="icon day" role="img" aria-label="Sunny, thin haze"></span><span class="icon storm" role="img" aria-label="Night thunderstorm"></span></div>
    <div class="row" style="top:90px"><span class="label">Temperature (°C)</span>
      <span class="cell"><span class="temp" style="background:var(--t19)">19 °</span></span><span class="cell"><span class="temp" style="background:var(--t19)">19 °</span></span><span class="cell"><span class="temp" style="background:var(--t25)">25 °</span></span><span class="cell"><span class="temp" style="background:var(--t29)">29 °</span></span><span class="cell"><span class="temp" style="background:var(--t32)">32 °</span></span><span class="cell"><span class="temp" style="background:var(--t32)">31 °</span></span><span class="cell"><span class="temp" style="background:var(--t27)">27 °</span></span></div>
    <div class="row" style="top:128px"><span class="label">Temperature felt (°C)</span>
      <span class="cell">21°</span><span class="cell">20°</span><span class="cell">25°</span><span class="cell">33°</span><span class="cell">35°</span><span class="cell">34°</span><span class="cell">32°</span></div>
    <div class="row" style="top:155px"><span class="label">Wind direction</span>
      <span class="cell arrow" style="transform:rotate(45deg)">↖</span><span class="cell arrow" style="transform:rotate(-20deg)">↖</span><span class="cell arrow" style="transform:rotate(-20deg)">↖</span><span class="cell arrow">←</span><span class="cell arrow">←</span><span class="cell arrow" style="transform:rotate(-10deg)">↖</span><span class="cell arrow" style="transform:rotate(-20deg)">↖</span></div>
    <div class="row" style="top:182px"><span class="label">Wind speed (km/h)</span>
      <span class="cell">7</span><span class="cell">9</span><span class="cell">13</span><span class="cell">11</span><span class="cell">11</span><span class="cell">10</span><span class="cell">5</span></div>
    <div class="row" style="top:208px"><span class="label">Wind gusts (km/h)</span>
      <span class="cell">8</span><span class="cell">15</span><span class="cell">15</span><span class="cell">11</span><span class="cell">25</span><span class="cell">27</span><span class="cell">6</span></div>
    <div class="row blue" style="top:234px"><span class="label">Precipitation (mm)</span>
      <span class="cell">-</span><span class="cell">-</span><span class="cell">-</span><span class="cell">-</span><span class="cell">-</span><span class="cell">-</span><span class="cell">-</span></div>
    <div class="row blue" style="top:260px"><span class="label">Precipitation probability</span>
      <span class="cell">0%</span><span class="cell">0%</span><span class="cell">0%</span><span class="cell">1%</span><span class="cell">17%</span><span class="cell">14%</span><span class="cell">19%</span></div>
    <div class="row" style="top:287px"><span class="label" style="line-height:14px">rainView<br><small style="font-size:10.5px">Precipitation distribution within 15 km</small></span>
      <svg class="ring" viewBox="0 0 48 42"><g fill="none" stroke="#444"><circle cx="24" cy="21" r="17"/><circle cx="24" cy="21" r="11"/><circle cx="24" cy="21" r="5"/></g></svg>
      <svg class="ring" viewBox="0 0 48 42"><g fill="none" stroke="#444"><circle cx="24" cy="21" r="17"/><circle cx="24" cy="21" r="11"/><circle cx="24" cy="21" r="5"/></g></svg>
      <svg class="ring" viewBox="0 0 48 42"><g fill="none" stroke="#444"><circle cx="24" cy="21" r="17"/><circle cx="24" cy="21" r="11"/><circle cx="24" cy="21" r="5"/></g></svg>
      <svg class="ring" viewBox="0 0 48 42"><g fill="none" stroke="#444"><circle cx="24" cy="21" r="17"/><circle cx="24" cy="21" r="11"/><circle cx="24" cy="21" r="5"/></g></svg>
      <svg class="ring" viewBox="0 0 48 42"><g fill="none" stroke="#444"><circle cx="24" cy="21" r="17"/><circle cx="24" cy="21" r="11"/><circle cx="24" cy="21" r="5"/></g></svg>
      <svg class="ring" viewBox="0 0 48 42"><path d="M30 6 L40 14 L34 22 L26 18Z M12 26 L20 34 L14 38Z" fill="#22d8f0"/><g fill="none" stroke="#444"><circle cx="24" cy="21" r="17"/><circle cx="24" cy="21" r="11"/><circle cx="24" cy="21" r="5"/></g></svg>
      <svg class="ring" viewBox="0 0 48 42"><path d="M8 12 Q24 -2 42 12 L36 18 Q24 8 14 18Z" fill="#22d8f0"/><g fill="none" stroke="#444"><circle cx="24" cy="21" r="17"/><circle cx="24" cy="21" r="11"/><circle cx="24" cy="21" r="5"/></g></svg>
    </div>
    <div class="abs band"><span>Additional parameters</span><span>Detail</span></div>
    <div class="abs tools"><span>Show help</span><span>Bookmark this page</span><span>Share on Friendwall</span></div>
  </section>

  <section class="abs panel radar">
    <h2>Precipitation radar with lightning</h2>
    <div class="abs rule"></div>
    <div class="abs map" style="left:10px;top:46px;width:187px;height:182px" role="img" aria-label="Relief map of Switzerland with precipitation radar"></div>
    <p class="abs" style="left:232px;top:45px;font-size:15px">Local short-term precipitation forecast</p>
    <div class="abs map" style="left:232px;top:80px;width:122px;height:127px" role="img" aria-label="Local radar map centred on Basel"></div>
    <p class="abs" style="left:374px;top:80px"><span class="blue">0 mm</span> Precipitation in Basel at 11:30-12:40</p>
    <p class="abs" style="left:374px;top:107px;width:310px">The animation shows the distribution of precipitation for the next hour. Lightning of the past half hour is displayed as red crosses. Basel is located in the center.</p>
    <div class="abs tools" style="left:374px;top:206px"><span>Show help</span></div>
  </section>

  <section class="abs banner">
    <div class="abs promo">
      <div class="abs art" role="img" aria-label="Sun behind a rain cloud"></div>
      <div class="abs brand">Skyvantor</div>
      <div class="abs tagline">forecasts for your website</div>
      <ul class="abs perks"><li>free to use</li><li>easy to integrate</li><li>worldwide available</li><li>valuable weather<br>information</li></ul>
    </div>
    <div class="abs days">
      <div class="d"><div class="n">Wed</div><div class="dt">07.08</div><div class="wi" role="img" aria-label="Thunderstorm"></div><div class="hi">24 <small>°C</small></div><div class="lo">19 <small>°C</small></div><div class="mm">8 <small>mm</small></div></div>
      <div class="d"><div class="n">Thu</div><div class="dt">08.08</div><div class="wi cloud" role="img" aria-label="Cloudy with rain"></div><div class="hi">22 <small>°C</small></div><div class="lo">19 <small>°C</small></div><div class="mm">9 <small>mm</small></div></div>
      <div class="d"><div class="n">Fri</div><div class="dt">09.08</div><div class="wi" role="img" aria-label="Sun and showers"></div><div class="hi">23 <small>°C</small></div><div class="lo" style="background:#a8f05a">17 <small>°C</small></div><div class="mm">3 <small>mm</small></div></div>
    </div>
    <div class="abs users">
      <div class="hd">ALREADY USING</div>
      <div class="nm" style="left:34px;top:32px;font-size:21px;line-height:24px">Plorix<br>Gazette</div>
      <div class="nm" style="left:22px;top:98px;font-size:18px">tonvillage</div>
      <div class="nm" style="left:16px;top:142px;width:120px;height:46px;background:#dcdcdc;color:#333;font-size:19px;padding:10px 0 0 22px">valtrun</div>
    </div>
  </section>

  <aside class="abs side">
    <h3>Predicability</h3>
    <p>We now display the estimated forecast uncertainty in our 7 day forecast as coloured bar to indicate possible inaccurate or frequently changing forecasts. It considers uncertainties in pressure, precipitation, temperature, wind, larger scale patterns and climate inconsistency. For more information read our forum post about <span class="blue">predicability</span>.</p>
    <p class="blue" style="text-align:right;margin-top:2px">&gt;&gt;&gt;</p>
  </aside>
  <div class="abs more">Further reading:
    <ul><li>skyvantor for smartphones</li><li>skyvantor on Friendwall</li><li>Help pages and additional information</li></ul>
  </div>
</div>
</body>
</html>
```